Business Card Design

We like to use greens as you will see in our logo (but not TOO much green). We are a Dental Clinic in a somewhat eccentric community. We do not like the dated sharp designs which we see many dentists use. We're looking for something bright and fresh while still maintaining the integrity of the profession. Elegance is not necessarily what we are going for... we need for the design to be "mature" but also up-lifting.

See our logo.
Updates

Project Deadline Extended
Reason: We have 5 designs which we like. But we'd like to see a few more before committing to a design.

Project Deadline Extended
Reason: We are awaiting revisions to this project. We are still welcoming designs while we wait to see if designers are able to provide to us the revisions we require in order to proceed with a selection.

Target Market(s)

Younger families - ages late 20's to early 40's

Industry/Entity Type

Business

Contact Information for Business Card

Corwel T. Banfry DDS 2730 W. Halvert Rd. Ste. 7 Royal Oak, MI 48391 (248)555-0174 FX (248)555-0189 info@BrightwellDentalCareMi.com BrigthwellDentalCareMi.com on the back of the card we need an appointment reminder (For____ Date___ Time____) with "If you are unable to keep your appointment, kindly give 48 hours notice" at the bottom. No use of teeth in the design. DOUBLE SIDED DESIGN

Requirements
Should not have
• The use of pictures of teeth

```html
<!DOCTYPE html>
<html lang="en">
<head>
<meta charset="utf-8">
<title>Brightwell Dental Care – Business Card</title>
<link rel="stylesheet" href="https://fonts.googleapis.com/css2?family=Cinzel:wght@500&family=Open+Sans:ital,wght@0,400;0,600;0,700;1,400&display=swap">
<style>
  :root {
    --green-dark: #1e6b34;
    --green-mid: #2f8a3c;
    --green-lime: #8cc63f;
    --ink: #2b2b2b;
    --paper: #ffffff;
    --backdrop: #eeeeec;
    --line: #555555;
  }
  * { box-sizing: border-box; margin: 0; padding: 0; }
  html, body { width: 1200px; height: 1178px; overflow: hidden; }
  body {
    background: var(--backdrop);
    font-family: "Open Sans", Arial, sans-serif;
    color: var(--ink);
    position: relative;
  }
  .card {
    position: absolute;
    width: 917px;
    height: 525px;
    background: var(--paper);
    overflow: hidden;
    box-shadow: 0 2px 6px rgba(0,0,0,.18);
  }
  .card--front { left: 236px; top: 44px; }
  .card--back { left: 35px; top: 606px; }

  /* brand name */
  .brand { position: absolute; display: flex; align-items: center; gap: 14px; }
  .brand__dot { border-radius: 50%; background: var(--green-lime); flex: none; }
  .brand__name {
    font-weight: 600;
    color: var(--green-dark);
    line-height: 1.05;
  }
  .card--front .brand { left: 74px; top: 150px; }
  .card--front .brand__dot { width: 34px; height: 34px; }
  .card--front .brand__name { font-size: 40px; }
  .card--back .brand { left: 60px; top: 50px; }
  .card--back .brand__dot { width: 22px; height: 22px; }
  .card--back .brand__name { font-size: 27px; }

  /* front contact */
  .divider {
    position: absolute; left: 498px; top: 89px;
    width: 2px; height: 236px; background: #888;
  }
  .contact { position: absolute; left: 520px; top: 90px; list-style: none; }
  .contact li {
    display: flex; align-items: center; gap: 8px;
    font-size: 21px; height: 40px;
  }
  .contact svg { width: 18px; height: 18px; fill: var(--green-dark); flex: none; }
  .address {
    position: absolute; left: 520px; top: 264px;
    font-size: 21px; line-height: 31px; font-style: normal;
  }
  .wave { position: absolute; left: 0; top: 0; }
  .signature {
    position: absolute; left: 560px; top: 446px; width: 280px;
    text-align: center; color: var(--paper);
  }
  .signature__name { font-size: 30px; font-weight: 700; line-height: 1.2; }
  .signature__title { font-size: 23px; line-height: 1.35; }

  /* back appointment */
  .appt-title {
    position: absolute; left: 80px; top: 170px;
    font-family: "Cinzel", Georgia, serif; font-weight: 500;
    font-size: 32px; letter-spacing: 1px; color: var(--green-dark);
  }
  .field {
    position: absolute; left: 80px;
    display: flex; align-items: baseline; font-size: 24px;
  }
  .field__rule {
    display: inline-block; border-bottom: 2px dotted var(--line);
    margin: 0 8px;
  }
  .field--name { top: 244px; }
  .field--date { top: 310px; }
  .field--next { top: 374px; }
  .slot {
    position: absolute; height: 35px; border: 2px solid #666; border-radius: 5px;
  }
  .days { position: absolute; left: 740px; top: 0; list-style: none; }
  .days li {
    position: absolute; left: 0; width: 150px;
    display: flex; justify-content: flex-end; align-items: center; gap: 14px;
    font-size: 25px; font-weight: 600;
  }
  .days .slot { position: static; width: 56px; height: 34px; }
  .notice {
    position: absolute; left: 76px; top: 452px;
    font-size: 25px; font-style: italic;
  }
  .footer-band {
    position: absolute; left: 0; bottom: 0; width: 100%; height: 12px;
    background: var(--green-dark);
  }
</style>
</head>
<body>

<section class="card card--front" aria-label="Business card front">
  <div class="brand">
    <span class="brand__dot"></span>
    <span class="brand__name">Brightwell<br>Dental Care</span>
  </div>

  <div class="divider"></div>

  <ul class="contact">
    <li>
      <svg viewBox="0 0 24 24" aria-hidden="true"><path d="M6.6 10.8a15 15 0 0 0 6.6 6.6l2.2-2.2c.3-.3.7-.4 1-.2 1.1.4 2.3.6 3.6.6.6 0 1 .4 1 1V20c0 .6-.4 1-1 1A17 17 0 0 1 3 4c0-.6.4-1 1-1h3.5c.6 0 1 .4 1 1 0 1.3.2 2.5.6 3.6.1.3 0 .7-.2 1z"/></svg>
      (248)555-0174
    </li>
    <li>
      <svg viewBox="0 0 24 24" aria-hidden="true"><path d="M5 9h14l2 4v6h-3v-2H6v2H3v-6zM7 4h10l1 4H6zM6 14a1.5 1.5 0 1 0 0 .01zM18 14a1.5 1.5 0 1 0 0 .01z"/></svg>
      (248)555-0189
    </li>
    <li>
      <svg viewBox="0 0 24 24" aria-hidden="true"><path d="M2 6h20v12H2zm2 2v.5l8 5 8-5V8l-8 5z"/></svg>
      info@BrightwellDentalCareMi.com
    </li>
    <li>
      <svg viewBox="0 0 24 24" aria-hidden="true"><path d="M12 2a10 10 0 1 0 0 20 10 10 0 0 0 0-20zm0 2c1 1.3 1.8 3 2.1 5H9.9C10.2 7 11 5.3 12 4zM4.3 11h3.6c0 .7 0 1.4.1 2H4.3a8 8 0 0 1 0-2zm5.6 0h4.2v2H9.9zm6.2 0h3.6a8 8 0 0 1 0 2h-3.6zM9.9 15h4.2c-.3 2-1.1 3.7-2.1 5-1-1.3-1.8-3-2.1-5z"/></svg>
      BrigthwellDentalCareMi.com
    </li>
  </ul>

  <address class="address">
    2730 W. Halvert Rd.<br>
    Ste. 7 Royal Oak, MI 48391
  </address>

  <svg class="wave" width="917" height="525" viewBox="0 0 917 525" aria-hidden="true">
    <!-- lime stripe above the band -->
    <path d="M0 404 C160 434 320 466 440 440 C500 420 580 400 917 396" fill="none" stroke="var(--green-lime)" stroke-width="9"/>
    <!-- dark band -->
    <path d="M0 420 C160 450 320 496 440 470 C500 430 580 418 917 420 L917 525 L0 525 Z" fill="var(--green-dark)"/>
    <!-- inner stripes on the left only -->
    <path d="M0 452 C140 480 290 505 430 482" fill="none" stroke="var(--paper)" stroke-width="5"/>
    <path d="M0 468 C140 496 290 518 420 496" fill="none" stroke="var(--green-lime)" stroke-width="6"/>
  </svg>

  <div class="signature">
    <p class="signature__name">Corwel T. Banfry</p>
    <p class="signature__title">DDS</p>
  </div>
</section>

<section class="card card--back" aria-label="Appointment card back">
  <div class="brand">
    <span class="brand__dot"></span>
    <span class="brand__name">Brightwell<br>Dental Care</span>
  </div>

  <h2 class="appt-title">YOUR APPOINTMENT</h2>

  <div class="field field--name">Name :<span class="field__rule" style="width:505px"></span></div>
  <div class="field field--date">
    Date :<span class="field__rule" style="width:165px;margin-left:30px"></span>
    Time :<span class="field__rule" style="width:150px"></span>am / pm
  </div>
  <div class="field field--next">Next Appointment</div>
  <div class="slot" style="left:327px;top:374px;width:162px"></div>
  <div class="slot" style="left:528px;top:374px;width:164px"></div>

  <ul class="days">
    <li style="top:76px">MON <span class="slot"></span></li>
    <li style="top:140px">TUE <span class="slot"></span></li>
    <li style="top:202px">WED <span class="slot"></span></li>
    <li style="top:268px">THU <span class="slot"></span></li>
    <li style="top:324px">FRI <span class="slot"></span></li>
    <li style="top:379px">SAT <span class="slot"></span></li>
  </ul>

  <p class="notice">If you are unable to keep your appointment, kindly give 48 hours notice</p>
  <div class="footer-band"></div>
</section>

</body>
</html>
```